Brightway Haus Inc. Business Card Design

Brightway Haus Inc. is in search of a great clean design for our business cards!

Looking to incorporate our full logo and watermark on side one (however, I am open to having the text and watermark separated within the design.)

On side two, I am looking to have contact information (Name, Position, Phone #, Email, Website (www.thebrightwayhaus.ca). Can have the logo and/or watermark as part of the design if applicable.

Please add tagline "Where Shine Counts" on either side 1 or 2. This tagline can be in a sans serif, serif or cursive font as long as it compliments overall design. Capitalization can be title or sentence case depending on how it fits within the design.

Get creative!! Looking for a clean, crisp, premium design! Looking for a glossy card finish with spot UV features when printed. Cards will also be printed with rounded corners. Standard dimensions (3.5 x 2).

Target Market(s)

B2B - primary clients are business owners or property management corporations. (residential jobs are few and far between)

Industry/Entity Type

Business

Contact Information for Business Card

- clean, crisp design
- double sided
- spot UV accents and glossy finish upon printing
- standard business card size (3.5 x 2) with rounded corners
- please see project description for requirements per side

Font styles to use
Sans Serif

Requirements
Must have
• - adequate bleeds with print ready files
• - cohesive design elements between side 1 & 2
• - spot UV elements (can be on both sides or just one, use your discretion)
• - colour pallet should match the logo file provided
• - incorporate tagline "where shine counts" (this tagline can be in a serif or sans serif font as long as it is complimentary to the overall design.
Nice to have
• - Premium elements with a clean design
Should not have
• - Please omit cartoon or whimsical like designs, think premium.
• - Colours should not stray from the pallet of the provided logo.

```html
<!DOCTYPE html>
<html lang="en">
<head>
<meta charset="utf-8">
<title>Brightway Haus Inc. Business Cards</title>
<link rel="stylesheet" href="https://fonts.googleapis.com/css2?family=Roboto:wght@400;500;700&family=Open+Sans:wght@700&display=swap">
<style>
  :root {
    --backdrop: #3a332e;
    --card: #1b1e23;
    --teal: #2bbfc4;
    --navy: #28327a;
    --ink: #ffffff;
    --rule: #8a8f96;
  }
  html, body {
    margin: 0;
    padding: 0;
    width: 1200px;
    height: 769px;
    overflow: hidden;
    background: var(--backdrop);
  }
  .stage {
    position: relative;
    width: 1200px;
    height: 769px;
    font-family: "Roboto", sans-serif;
    color: var(--ink);
  }
  .card {
    position: absolute;
    top: 230px;
    width: 540px;
    height: 309px;
    background: var(--card);
    border-radius: 14px;
    overflow: hidden;
  }
  .card--contact { left: 45px; }
  .card--brand { left: 615px; }

  .brand-square {
    position: absolute;
    top: 36px;
    right: 58px;
    width: 92px;
    height: 92px;
    background: var(--teal);
  }
  .accent-bar {
    position: absolute;
    left: 0;
    top: 200px;
    width: 8px;
    height: 30px;
    background: var(--teal);
  }
  .person {
    position: absolute;
    left: 40px;
    top: 176px;
  }
  .person__name {
    font-weight: 700;
    font-size: 19px;
    color: var(--teal);
    letter-spacing: 0.5px;
    margin: 0;
  }
  .person__role {
    font-size: 12px;
    font-weight: 500;
    color: var(--navy);
    letter-spacing: 0.6px;
    margin: 1px 0 0;
  }
  .contact-list {
    position: absolute;
    left: 44px;
    top: 225px;
    list-style: none;
    margin: 0;
    padding: 0;
    font-size: 13px;
    line-height: 15.5px;
  }
  .contact-list li {
    display: flex;
    align-items: center;
    gap: 9px;
  }
  .contact-list svg {
    width: 11px;
    height: 11px;
    fill: var(--teal);
    flex: none;
  }
  .divider {
    position: absolute;
    left: 262px;
    top: 230px;
    width: 1px;
    height: 34px;
    background: var(--rule);
  }
  .address {
    position: absolute;
    left: 278px;
    top: 228px;
    font-size: 13px;
    line-height: 17px;
    margin: 0;
    font-style: normal;
  }

  .wordmark {
    position: absolute;
    left: 0;
    right: 0;
    top: 112px;
    display: flex;
    justify-content: center;
    align-items: center;
    gap: 12px;
  }
  .wordmark__square {
    width: 34px;
    height: 34px;
    background: var(--teal);
  }
  .wordmark__name {
    font-family: "Open Sans", sans-serif;
    font-weight: 700;
    font-size: 34px;
    color: var(--teal);
    letter-spacing: -0.5px;
    margin: 0;
  }
  .tagline {
    position: absolute;
    left: 0;
    right: 0;
    top: 178px;
    display: flex;
    justify-content: center;
    align-items: center;
    gap: 8px;
    font-size: 14px;
  }
  .tagline__rule {
    width: 120px;
    height: 1px;
    background: linear-gradient(90deg, transparent, var(--rule));
  }
  .tagline__rule--right {
    background: linear-gradient(90deg, var(--rule), transparent);
  }
</style>
</head>
<body>
<main class="stage">
  <section class="card card--contact" aria-label="Contact side">
    <div class="brand-square"></div>
    <div class="accent-bar"></div>
    <div class="person">
      <p class="person__name">MARA ELLISON</p>
      <p class="person__role">CEO/FOUNDER</p>
    </div>
    <ul class="contact-list">
      <li><svg viewBox="0 0 12 12"><path d="M2 1h3l1 3-1.5 1a7 7 0 0 0 2.5 2.5L8 6l3 1v3a1 1 0 0 1-1 1A9 9 0 0 1 1 2a1 1 0 0 1 1-1z"/></svg>604 555 0127</li>
      <li><svg viewBox="0 0 12 12"><path d="M3 0h6a1 1 0 0 1 1 1v10a1 1 0 0 1-1 1H3a1 1 0 0 1-1-1V1a1 1 0 0 1 1-1zm0 2v7h6V2z"/></svg>604 555 0183</li>
      <li><svg viewBox="0 0 12 12"><path d="M3 0h6v3h2v7H1V3h2zm1 1v2h4V1zM3 6v2h6V6z"/></svg>604 555 0149</li>
      <li><svg viewBox="0 0 12 12"><path d="M0 2h12v8H0zm1 1v.5l5 3.5 5-3.5V3z"/></svg>hello@thebrightwayhaus.ca</li>
      <li><svg viewBox="0 0 12 12"><circle cx="6" cy="6" r="5.5"/></svg>www.thebrightwayhaus.ca</li>
    </ul>
    <div class="divider"></div>
    <address class="address">412 Harbourview Road<br>Vancouver, BC V6B 2K9</address>
  </section>

  <section class="card card--brand" aria-label="Brand side">
    <div class="wordmark">
      <div class="wordmark__square"></div>
      <p class="wordmark__name">BRIGHTWAY HAUS INC.</p>
    </div>
    <div class="tagline">
      <span class="tagline__rule"></span>
      <span>Where Shine Counts</span>
      <span class="tagline__rule tagline__rule--right"></span>
    </div>
  </section>
</main>
</body>
</html>
```